Aunt Roula's Bakery

I am about to create a luxury boutique that specializes in cake baking and cupcake
and ready for parties and special events and order delivery
the logo has already made

Boutique

Email:auntroulasbakery@mailbox-example.net
Instagram: aunt_roula_bakery
Twitter: xxxxxxx
WhatsApp: xxxxxxx

Requirements
Must have
• luxury design

```html
<!DOCTYPE html>
<html lang="en">
<head>
<meta charset="utf-8">
<title>Aunt Roula's Bakery – Business Card</title>
<link href="https://fonts.googleapis.com/css2?family=Open+Sans:wght@400;700&display=swap" rel="stylesheet">
<style>
  :root {
    --backdrop: #e9e9e9;
    --card: #ebebeb;
    --slate: #77776f;
    --slate-text: #6f6f69;
    --rose: #d98fa5;
    --rose-pale: #ecd3da;
    --white: #ffffff;
  }
  * { margin: 0; padding: 0; box-sizing: border-box; }
  html, body {
    width: 1200px; height: 782px; overflow: hidden;
    background: var(--backdrop);
  }
  .stage { position: relative; width: 1200px; height: 782px; }

  .card {
    position: absolute;
    width: 326px; height: 567px;
    background: var(--card);
    box-shadow: 0 2px 10px rgba(0,0,0,0.12);
    font-family: "Open Sans", Arial, sans-serif;
    color: var(--slate-text);
    text-align: center;
  }
  .card--upright { left: 710px; top: 85px; }
  .card--turned {
    left: calc(409.5px - 163px); top: calc(495px - 283.5px);
    transform: rotate(90deg) scale(0.97);
  }

  .brand { position: absolute; left: 0; top: 30px; width: 100%; }
  .brand__dot {
    width: 48px; height: 48px; margin: 0 auto;
    border-radius: 50%; background: var(--rose);
  }
  .brand__name {
    margin-top: 26px;
    font-weight: 400; font-size: 26px; line-height: 32px;
    color: var(--slate); letter-spacing: 0.5px;
  }
  .brand__name span {
    display: block; font-size: 16px; line-height: 22px; letter-spacing: 7px;
  }

  .nameband { position: absolute; left: 0; top: 236px; width: 100%; }
  .nameband__line { height: 2px; background: var(--rose); margin: 0 6px; }
  .nameband__bar {
    margin-top: 6px; height: 56px; background: var(--slate);
    padding-top: 6px;
  }
  .nameband__line--below { margin-top: 2px; }
  .nameband__name { color: var(--white); font-weight: 700; font-size: 20px; line-height: 26px; letter-spacing: 0.5px; }
  .nameband__role { color: var(--rose); font-size: 13px; line-height: 16px; }

  .contacts { position: absolute; left: 0; top: 333px; width: 100%; }
  .contacts__icons { display: flex; justify-content: center; gap: 3px; margin-bottom: 4px; }
  .contacts__icon { width: 9px; height: 9px; background: var(--rose); border-radius: 2px; }
  .contacts__line { font-size: 15.5px; line-height: 20.5px; }

  .ornament {
    position: absolute; left: 30px; top: 450px; width: 266px; height: 92px;
    background: linear-gradient(180deg, var(--rose-pale) 0%, rgba(236,211,218,0.35) 100%);
    border-radius: 4px;
  }
</style>
</head>
<body>
<main class="stage">

  <article class="card card--turned" aria-label="Business card, turned">
    <div class="brand">
      <div class="brand__dot"></div>
      <p class="brand__name">AUNT ROULA'S<span>BAKERY</span></p>
    </div>
    <div class="nameband">
      <div class="nameband__line"></div>
      <div class="nameband__bar">
        <p class="nameband__name">AUNT ROULA</p>
        <p class="nameband__role">OWNER</p>
      </div>
      <div class="nameband__line nameband__line--below"></div>
    </div>
    <div class="contacts">
      <div class="contacts__icons"><span class="contacts__icon"></span><span class="contacts__icon"></span><span class="contacts__icon"></span><span class="contacts__icon"></span></div>
      <p class="contacts__line">xxxxxxx</p>
      <p class="contacts__line">xxxxxxx</p>
      <p class="contacts__line">aunt_roula_bakery</p>
      <p class="contacts__line">auntroulasbakery@mailbox-example.net</p>
    </div>
    <div class="ornament" role="img" aria-label="Pink scrollwork ornament"></div>
  </article>

  <article class="card card--upright" aria-label="Business card">
    <div class="brand">
      <div class="brand__dot"></div>
      <p class="brand__name">AUNT ROULA'S<span>BAKERY</span></p>
    </div>
    <div class="nameband">
      <div class="nameband__line"></div>
      <div class="nameband__bar">
        <p class="nameband__name">AUNT ROULA</p>
        <p class="nameband__role">OWNER</p>
      </div>
      <div class="nameband__line nameband__line--below"></div>
    </div>
    <div class="contacts">
      <div class="contacts__icons"><span class="contacts__icon"></span><span class="contacts__icon"></span><span class="contacts__icon"></span><span class="contacts__icon"></span></div>
      <p class="contacts__line">xxxxxxx</p>
      <p class="contacts__line">xxxxxxx</p>
      <p class="contacts__line">aunt_roula_bakery</p>
      <p class="contacts__line">auntroulasbakery@mailbox-example.net</p>
    </div>
    <div class="ornament" role="img" aria-label="Pink scrollwork ornament"></div>
  </article>

</main>
</body>
</html>
```